Business Card Design Can you design a business card design? Looking for something unique and differe

Can you design a business card design? Looking for something unique and different. Can you design a business card design? Looking for something unique and different.Can you design a business card design? Looking for something unique and different.Can you design a business card design? Looking for something unique and different.Can you design a business card design? Looking for something unique and different.Can you design a business card design? Looking for something unique and different.

Industry/Entity Type

Business

Contact Information for Business Card

Can you design a business card design? Looking for something unique and different.

Font styles to use
Serif

```html
<!DOCTYPE html>
<html lang="en">
<head>
<meta charset="utf-8">
<title>Business Card – Dosewell</title>
<link rel="stylesheet" href="https://fonts.googleapis.com/css2?family=Quicksand:wght@600;700&family=Open+Sans:ital,wght@0,400;1,400&display=swap">
<style>
  :root {
    --page-bg: #e8e5e2;
    --card-light: #e6e3e2;
    --card-light-edge: #d9d5d4;
    --panel-dark: #121114;
    --accent-purple: #8a6b96;
    --accent-purple-deep: #6a4f78;
    --name-purple: #5b4466;
    --text-ink: #1d1b1f;
    --icon-ink: #5e5a62;
  }
  * { margin: 0; padding: 0; box-sizing: border-box; }
  html, body {
    width: 1200px;
    height: 970px;
    overflow: hidden;
    background: var(--page-bg);
  }
  .card {
    position: absolute;
    left: 100px;
    top: 207px;
    width: 1000px;
    height: 556px;
    background: linear-gradient(135deg, var(--card-light) 0%, #eeecea 55%, var(--card-light-edge) 100%);
    box-shadow: 0 10px 30px rgba(0,0,0,0.15);
    overflow: hidden;
  }
  .card-panel {
    position: absolute;
    inset: 0;
    width: 1000px;
    height: 556px;
  }
  .brand-name {
    position: absolute;
    left: 0;
    width: 450px;
    top: 318px;
    text-align: center;
    font-family: "Quicksand", sans-serif;
    font-weight: 700;
    font-size: 50px;
    color: var(--accent-purple);
    letter-spacing: 0.5px;
  }
  .holder {
    position: absolute;
    left: 556px;
    top: 78px;
  }
  .holder-name {
    font-family: "Quicksand", sans-serif;
    font-weight: 700;
    font-size: 32px;
    color: var(--name-purple);
  }
  .holder-role {
    margin-top: 8px;
    font-family: "Open Sans", sans-serif;
    font-style: italic;
    font-size: 19px;
    color: var(--text-ink);
  }
  .contact-list {
    position: absolute;
    left: 556px;
    top: 276px;
    list-style: none;
    font-family: "Open Sans", sans-serif;
    font-size: 22px;
    color: var(--text-ink);
  }
  .contact-item {
    display: flex;
    align-items: center;
    height: 34px;
  }
  .contact-icon {
    width: 24px;
    height: 20px;
    margin-right: 28px;
    fill: var(--icon-ink);
  }
  .address {
    position: absolute;
    left: 556px;
    top: 404px;
    font-family: "Open Sans", sans-serif;
    font-size: 22px;
    line-height: 34px;
    color: var(--text-ink);
  }
</style>
</head>
<body>
  <div class="card">
    <svg class="card-panel" viewBox="0 0 1000 556" aria-hidden="true">
      <path class="panel-accent" fill="var(--accent-purple)"
        d="M0 0 H462 C505 120 515 250 493 330 C480 400 455 480 439 556 H0 Z"/>
      <path class="panel-dark" fill="var(--panel-dark)"
        d="M0 0 H447 C490 120 500 250 478 330 C465 400 440 480 424 556 H0 Z"/>
    </svg>

    <div class="brand-name">Dosewell</div>

    <div class="holder">
      <div class="holder-name">Your Long Name</div>
      <div class="holder-role">Managing Director</div>
    </div>

    <ul class="contact-list">
      <li class="contact-item">
        <svg class="contact-icon" viewBox="0 0 24 20"><path d="M2 6 C2 2 22 2 22 6 L22 8 L17 8 L17 6 L7 6 L7 8 L2 8 Z M6 9 H18 L21 18 H3 Z"/></svg>
        00.00.00.0000
      </li>
      <li class="contact-item">
        <svg class="contact-icon" viewBox="0 0 24 20"><path d="M1 3 H23 V17 H1 Z M2 4 L12 12 L22 4" stroke="var(--card-light)" stroke-width="1.5"/></svg>
        yourname@yourwebsite.com
      </li>
      <li class="contact-item">
        <svg class="contact-icon" viewBox="0 0 24 20"><circle cx="12" cy="10" r="9"/><path d="M3 10 H21 M12 1 V19 M12 1 C7 5 7 15 12 19 M12 1 C17 5 17 15 12 19" stroke="var(--card-light)" stroke-width="1.2" fill="none"/></svg>
        www.yourwebsite.com
      </li>
    </ul>

    <p class="address">Your Commercial or office address<br>in just two line with pincode</p>
  </div>
</body>
</html>
```